Website for courses for men for making money, health, fitness

I require a website which is going to be a mix of a crypto currency website and website aimed at providing men with money making, health, relationship advice courses and content

The name isn't decided yet so for now please call it something like

KESTREL YARD

A platform dedicated to making men wealthy, physically strong, mentally tough & successful with women

In the top right, I need it to show how many points they have, they must buy points in order to use them to claim the courses.

WHAT WE DO

Kestrel yard is a platform where you can learn everything you need about business, making money, crypto currency, fitness, health, mental toughness and resilience and how to be successful with women all in one place

HOW WILL THIS WORK & WHY SHOULD I BUY POINTS?

xxxxxxxxxxxxxxxxxxxxxxxx
xxxxxxxxxxxxxxxxxxxxxxx
xxxxxxxxxxxxxxxxxxxxx

AFFILIATE SCHEME

EARN UP TO $125 DOLLARS PER PERSON WHO SIGNS UP THROUGH YOUR LINK

START EARNING NOW - button
______________________________________________________

BUY POINTS
(A maximum of only $250 worth of points can be purchased per person until the platform goes fully live)

ROAD MAP & THE MODEL

2023

Q1 - PRE BUY IN FOR POINTS

Q2 - FULL WEBSITE LAUNCH

Q3 - APP LAUNCH

Q4 - IN APP ADVERT LAUNCH

It must have a very slick and sharp eye catching look, and be designed to convert people into purchasing points

some ideas of the feel of the website -

https://brivaloo.io/
https://nestorly.style/
https://plumwick.trelvanta.com/

```html
<!DOCTYPE html>
<html lang="en">
<head>
<meta charset="utf-8">
<title>Kestrel Yard</title>
<link rel="stylesheet" href="https://fonts.googleapis.com/css2?family=Exo+2:wght@500;600;700&family=Mulish:wght@400;600;700&display=swap">
<style>
:root{
  --bg:#0e0a18;
  --bg-deep:#08060f;
  --purple:#d07bf7;
  --purple-soft:#a95fd0;
  --purple-dark:#3a2352;
  --white:#ffffff;
  --text:#e6e1ee;
  --muted:#b9b2c6;
  --line:#2c2540;
}
*{box-sizing:border-box;margin:0;padding:0}
html,body{width:1200px;height:4843px;overflow:hidden}
body{background:var(--bg);color:var(--text);font-family:"Mulish",sans-serif;position:relative}
.abs{position:absolute}
.heading{font-family:"Exo 2",sans-serif;font-weight:600;color:var(--white);text-transform:uppercase;letter-spacing:.5px}
.btn{position:absolute;display:flex;align-items:center;justify-content:center;background:var(--purple);color:var(--white);border-radius:30px;font-family:"Mulish",sans-serif;font-weight:700;font-size:14px;text-transform:uppercase;text-decoration:none;letter-spacing:.3px}
.body-copy{font-size:14.5px;line-height:30px;color:var(--text)}

/* header */
.site-header .logo{left:109px;top:38px;font-family:"Exo 2",sans-serif;font-weight:700;font-size:30px;color:var(--white);letter-spacing:1px}
.nav a{position:absolute;top:44px;font-size:15px;font-weight:600;color:var(--white);text-decoration:none}
.nav a.active{color:var(--purple)}
.hero-glow{left:0;top:0;width:1200px;height:760px;background:radial-gradient(ellipse at 78% 35%,#3a1f55 0%,rgba(30,16,48,.6) 25%,rgba(14,10,24,0) 55%),linear-gradient(180deg,#0c0916 0%,#150f22 60%,var(--bg) 100%)}
.hero-title{left:108px;top:272px;font-size:64px;line-height:78px}
.hero-sub{left:115px;top:430px;width:460px;font-size:15px;line-height:25px;color:var(--text)}
.hero-art{left:677px;top:282px;width:367px;height:395px;border-radius:50%;background:radial-gradient(circle at 50% 45%,#8d6aa8 0%,#4b2e68 30%,#261638 60%,rgba(14,10,24,0) 75%)}

/* feature groups */
.feature-art{position:absolute;width:474px;height:475px}
.feature-art svg{position:absolute;left:0;top:0}
.feature-art .photo{position:absolute;border-radius:44% 30% 46% 32%/30% 40% 34% 46%}
.photo-cash{left:135px;top:45px;width:269px;height:350px;transform:rotate(-14deg);background:linear-gradient(150deg,#9aa08a 0%,#6b6e5c 35%,#3c3430 70%,#c7c2a8 100%)}
.photo-hands{left:70px;top:55px;width:267px;height:340px;transform:rotate(14deg);background:linear-gradient(160deg,#d6cbc2 0%,#c89a84 40%,#b52a2e 60%,#a89c94 100%)}
.photo-deal{left:135px;top:45px;width:269px;height:350px;transform:rotate(-14deg);background:linear-gradient(150deg,#e9e4dc 0%,#3a3d52 35%,#2a2d3e 55%,#c9843f 85%,#e6b27a 100%)}

.feature-text .heading{font-size:34px;line-height:50px}

/* roadmap */
.roadmap-title{left:0;width:1200px;top:2790px;text-align:center;font-size:34px}
.year-pill{left:549px;top:2887px;width:109px;height:29px;border-radius:15px;background:var(--purple);color:var(--white);font-family:"Exo 2",sans-serif;font-weight:600;font-size:17px;display:flex;align-items:center;justify-content:center}
.timeline{left:598px;top:2916px;width:4px;height:684px;background:#2b2540;border-radius:2px}
.quarter{position:absolute;width:58px;height:58px;border-radius:50%;background:var(--purple);color:var(--white);font-family:"Exo 2",sans-serif;font-weight:600;font-size:20px;display:flex;align-items:center;justify-content:center;left:571px}
.dots{position:absolute;width:44px;border-top:3px dotted var(--muted)}
.milestone{position:absolute;width:320px}
.milestone h3{font-family:"Exo 2",sans-serif;font-weight:600;font-size:21px;color:var(--white);text-transform:uppercase;margin-bottom:10px}
.milestone p{font-size:12.5px;line-height:24px;color:var(--text)}

/* buy points */
.phone-art{left:109px;top:3794px;width:446px;height:540px}
.phone-art .pill{position:absolute;top:75px;width:140px;height:390px;border-radius:70px;background:var(--purple)}
.phone-art .device{position:absolute;left:82px;top:0;width:280px;height:540px;border:9px solid var(--white);border-radius:34px;background:linear-gradient(180deg,#232552 0%,#2c2e66 45%,#5a3aa0 70%,#1b1c40 100%)}
.buy-title{left:611px;top:3870px;font-size:36px}
.buy-note{left:611px;top:3937px;width:470px;font-weight:700;font-size:22px;line-height:34px;color:var(--white)}

/* footer */
.footer-glow{left:0;top:4480px;width:1200px;height:363px;background:linear-gradient(180deg,var(--bg) 0%,#0b0813 100%)}
.footer-logo{left:0;width:1200px;top:4540px;text-align:center;font-family:"Exo 2",sans-serif;font-weight:700;font-size:32px;color:var(--white);letter-spacing:1px}
.footer-nav a{position:absolute;top:4618px;font-size:15px;font-weight:600;color:var(--white);text-decoration:none}
.footer-nav a.active{color:var(--purple)}
.social{position:absolute;top:4677px;width:34px;height:34px;border-radius:50%;background:var(--purple)}
.copyright{left:0;width:1200px;top:4758px;text-align:center;font-size:13px;color:var(--white)}
.copyright a{color:var(--purple)}
</style>
</head>
<body>

<div class="abs hero-glow"></div>

<header class="site-header">
  <div class="abs logo">KESTREL YARD</div>
  <nav class="nav">
    <a href="#" class="active" style="left:409px">Home</a>
    <a href="#" style="left:496px">About Us</a>
    <a href="#" style="left:606px">Our Services</a>
    <a href="#" style="left:739px">Our Blog</a>
    <a href="#" style="left:844px">Contact Us</a>
  </nav>
  <a href="#" class="btn" style="left:959px;top:32px;width:130px;height:39px;font-size:11.5px">Buy Points</a>
</header>

<section class="hero">
  <h1 class="abs heading hero-title">Welcome to<br>Kestrel Yard.</h1>
  <p class="abs hero-sub">A platform dedicated to making men wealthy, physically strong, mentally tough &amp; successful with women</p>
  <a href="#" class="btn" style="left:113px;top:504px;width:165px;height:51px">Get Started</a>
  <div class="abs hero-art" role="img" aria-label="Glowing purple coin on a round pedestal"></div>
</section>

<!-- What we do -->
<section>
  <div class="feature-art" style="left:109px;top:870px">
    <svg width="474" height="475" viewBox="0 0 474 475">
      <polygon points="140,20 400,10 430,380 190,455" fill="#120d1e" stroke="#231b33" stroke-width="2"/>
      <polygon points="60,55 20,70 150,475 300,425" fill="none" stroke="var(--purple-soft)" stroke-width="2"/>
      <circle cx="383" cy="135" r="90" fill="var(--purple)"/>
      <circle cx="306" cy="26" r="25" fill="var(--purple)"/>
      <circle cx="100" cy="335" r="100" fill="var(--purple)"/>
    </svg>
    <div class="photo photo-cash" role="img" aria-label="Photo of a smiling woman at a laptop with banknotes flying around her"></div>
  </div>
  <div class="abs feature-text" style="left:626px;top:950px">
    <h2 class="heading">What We Do</h2>
  </div>
  <p class="abs body-copy" style="left:628px;top:1019px;width:470px">Kestrel yard is a platform where you can learn everything you need about business, making money, crypto currency, fitness, health, mental toughness and resilience and how to be successful with women all in one place</p>
  <a href="#" class="btn" style="left:628px;top:1169px;width:167px;height:53px">Leran More</a>
</section>

<!-- How will this work -->
<section>
  <div class="abs feature-text" style="left:107px;top:1527px">
    <h2 class="heading">How will this work &amp;<br>why should I buy points?</h2>
  </div>
  <p class="abs body-copy" style="left:107px;top:1647px;width:470px">Lorem ipsum dolor sit amet, consectetur adipiscing elit, sed do eiusmod tempor incididunt ut labore et dolore magna aliqua. Quis ipsum suspendisse ultrices gravida. Risus commodo viverra maecenas accumsan lacus vel facilisis.</p>
  <a href="#" class="btn" style="left:105px;top:1792px;width:166px;height:52px">Leran More</a>
  <div class="feature-art" style="left:628px;top:1442px">
    <svg width="474" height="475" viewBox="0 0 474 475">
      <polygon points="60,10 330,15 300,400 40,430" fill="#120d1e" stroke="#231b33" stroke-width="2"/>
      <polygon points="410,55 450,70 300,470 130,410" fill="none" stroke="var(--purple-soft)" stroke-width="2"/>
      <circle cx="90" cy="124" r="90" fill="var(--purple)"/>
      <circle cx="165" cy="24" r="28" fill="var(--purple)"/>
      <circle cx="374" cy="335" r="100" fill="var(--purple)"/>
    </svg>
    <div class="photo photo-hands" role="img" aria-label="Photo of cupped hands holding a red heart"></div>
  </div>
</section>

<!-- Affiliate scheme -->
<section>
  <div class="feature-art" style="left:102px;top:2049px">
    <svg width="474" height="475" viewBox="0 0 474 475">
      <polygon points="140,20 400,10 430,380 190,455" fill="#120d1e" stroke="#231b33" stroke-width="2"/>
      <polygon points="60,55 20,70 150,475 300,425" fill="none" stroke="var(--purple-soft)" stroke-width="2"/>
      <circle cx="383" cy="135" r="90" fill="var(--purple)"/>
      <circle cx="306" cy="26" r="25" fill="var(--purple)"/>
      <circle cx="100" cy="335" r="100" fill="var(--purple)"/>
    </svg>
    <div class="photo photo-deal" role="img" aria-label="Photo of two business people shaking hands over documents"></div>
  </div>
  <div class="abs feature-text" style="left:630px;top:2138px">
    <h2 class="heading">Affiliate Scheme</h2>
  </div>
  <p class="abs" style="left:630px;top:2204px;width:430px;font-size:19px;line-height:30px;color:var(--white);text-transform:uppercase">Earn up to $125 dollars per person who signs up through your link</p>
  <p class="abs body-copy" style="left:630px;top:2275px;width:470px">Lorem ipsum dolor sit amet, consectetur adipiscing elit, sed do eiusmod tempor incididunt ut labore et dolore magna aliqua. Quis ipsum suspendisse ultrices gravida. Risus commodo viverra maecenas accumsan lacus vel facilisis.</p>
  <a href="#" class="btn" style="left:632px;top:2421px;width:223px;height:51px">Start Earning Now</a>
</section>

<!-- Road map -->
<section>
  <h2 class="abs heading roadmap-title">Road Map</h2>
  <div class="abs year-pill">2023</div>
  <div class="abs timeline"></div>

  <div class="quarter" style="top:3020px">Q1</div>
  <div class="dots" style="left:634px;top:3048px"></div>
  <div class="milestone" style="left:720px;top:2956px">
    <h3>Pre Buy In For Points</h3>
    <p>Lorem ipsum dolor sit amet, consectetur adipiscing elit, sed do eiusmod tempor incididunt ut labore et dolore magna aliqua. Quis ipsum suspendisse ultrices gravida.</p>
  </div>

  <div class="quarter" style="top:3161px">Q2</div>
  <div class="dots" style="left:522px;top:3189px"></div>
  <div class="milestone" style="left:188px;top:3110px">
    <h3>Full Website Launch</h3>
    <p>Lorem ipsum dolor sit amet, consectetur adipiscing elit, sed do eiusmod tempor incididunt ut labore et dolore magna aliqua. Quis ipsum suspendisse ultrices gravida.</p>
  </div>

  <div class="quarter" style="top:3306px">Q3</div>
  <div class="dots" style="left:634px;top:3334px"></div>
  <div class="milestone" style="left:720px;top:3248px">
    <h3>App Launch</h3>
    <p>Lorem ipsum dolor sit amet, consectetur adipiscing elit, sed do eiusmod tempor incididunt ut labore et dolore magna aliqua. Quis ipsum suspendisse ultrices gravida.</p>
  </div>

  <div class="quarter" style="top:3456px">Q4</div>
  <div class="dots" style="left:522px;top:3484px"></div>
  <div class="milestone" style="left:188px;top:3402px">
    <h3>In App Advert Launch</h3>
    <p>Lorem ipsum dolor sit amet, consectetur adipiscing elit, sed do eiusmod tempor incididunt ut labore et dolore magna aliqua. Quis ipsum suspendisse ultrices gravida.</p>
  </div>
</section>

<!-- Buy points -->
<section>
  <div class="abs phone-art">
    <div class="pill" style="left:0"></div>
    <div class="pill" style="left:306px"></div>
    <div class="device" role="img" aria-label="Smartphone showing a dark trading app with price charts"></div>
  </div>
  <h2 class="abs heading buy-title">Buy Points</h2>
  <p class="abs buy-note">(A maximum of only $250 worth of points can be purchased per person until the platform goes fully live)</p>
  <p class="abs body-copy" style="left:609px;top:4043px;width:470px;font-size:14px;line-height:26px">Lorem ipsum dolor sit amet, consectetur adipiscing elit, sed do eiusmod tempor incididunt ut labore et dolore magna aliqua. Quis ipsum suspendisse ultrices gravida. Risus commodo viverra maecenas accumsan lacus vel facilisis. Lorem ipsum dolor sit amet, consectetur adipiscing elit, sed do eiusmod tempor incididunt ut labore et dolore magna aliqua.</p>
  <a href="#" class="btn" style="left:613px;top:4219px;width:163px;height:51px">Leran More</a>
</section>

<!-- Footer -->
<footer>
  <div class="abs footer-glow"></div>
  <div class="abs footer-logo">KESTREL YARD</div>
  <nav class="footer-nav">
    <a href="#" class="active" style="left:344px">Home</a>
    <a href="#" style="left:430px">About Us</a>
    <a href="#" style="left:540px">Our Services</a>
    <a href="#" style="left:672px">Our Blog</a>
    <a href="#" style="left:778px">Contact Us</a>
  </nav>
  <span class="social" style="left:500px" aria-label="Social link"></span>
  <span class="social" style="left:554px" aria-label="Social link"></span>
  <span class="social" style="left:609px" aria-label="Social link"></span>
  <span class="social" style="left:662px" aria-label="Social link"></span>
  <p class="abs copyright">© Copyrights 2022 <a href="#">Kestrel Yard</a> &nbsp;|&nbsp;&nbsp; All Rights Reserved</p>
</footer>

</body>
</html>
```